Fast-casual chicken restaurant Crisp Harbor needs a catering menu design

We need a catering menu designed for Crisp Harbor. We are looking to design a 24x36in landscape menu board for our new catering menu. The catering memo attached includes our catering menu and Crisp Harbor branding. More information about our brand can be found at https://crispharbor-eats.example/.

```html
<!DOCTYPE html>
<html lang="en">
<head>
<meta charset="utf-8">
<title>Crisp Harbor Catering Menu</title>
<link href="https://fonts.googleapis.com/css2?family=Montserrat:ital,wght@0,400;0,500;0,600;0,700;0,800;0,900;1,700&display=swap" rel="stylesheet">
<style>
:root{
  --yellow:#fccb2e;
  --red:#d43b2c;
  --white:#ffffff;
  --navy:#2a3a5e;
  --wood:#7a4a26;
  --wood-dark:#4a2a14;
}
*{margin:0;padding:0;box-sizing:border-box}
html,body{width:1200px;height:800px;overflow:hidden;background:#fff}
.board{position:relative;width:1200px;height:800px;overflow:hidden;font-family:"Montserrat",sans-serif;
  background:linear-gradient(180deg,var(--wood) 0%,var(--wood-dark) 50%,var(--wood) 100%)}
.photo{position:absolute}
.photo-top{left:0;top:0;width:1200px;height:124px;background:linear-gradient(90deg,#c9742c,#8a3a1a 20%,#c98a3c 50%,#8a3a1a 80%,#c9742c)}
.photo-bottom{left:0;top:700px;width:1200px;height:100px;background:linear-gradient(90deg,#a8321c,#c25a28 30%,#d9b47a 50%,#c25a28 70%,#a8321c)}
.photo-platter{left:490px;top:0;width:224px;height:182px;z-index:2;border-radius:0 0 10px 10px;background:radial-gradient(ellipse at 50% 45%,#a4461e,#d7963f 70%,#eee 100%)}
.panel{position:absolute;left:74px;top:124px;width:1054px;height:576px;background:var(--yellow)}
.title{position:absolute;left:0;width:1200px;top:188px;text-align:center;color:var(--red);font-weight:900;font-size:68px;letter-spacing:6px;line-height:1}
.section-head{position:absolute;color:var(--white);font-weight:800;font-size:21px;letter-spacing:3px;line-height:1;display:flex;align-items:center;white-space:nowrap}
.section-head .rule{height:3px;background:var(--white);margin-left:20px}
.note{position:absolute;left:130px;top:292px;font-size:9px;font-weight:700;font-style:italic;color:var(--navy);letter-spacing:.3px;white-space:nowrap}
.option{position:absolute;top:318px;width:150px;height:180px}
.option .notch{position:absolute;left:-26px;top:0;width:20px;height:160px}
.option .label{position:absolute;top:15px;left:0;font-size:10px;letter-spacing:1.5px;color:var(--red);font-weight:500}
.option .name{position:absolute;top:28px;left:0;font-size:23px;font-weight:900;color:var(--red)}
.option .items{position:absolute;top:62px;left:0;font-size:13px;font-weight:600;color:var(--red);line-height:14px;list-style:none;white-space:nowrap}
.option .price{position:absolute;top:162px;left:0;font-size:11.5px;letter-spacing:2px;color:var(--red);font-weight:500;white-space:nowrap}
.package{position:absolute;top:294px;height:215px;background:var(--red);border-radius:0 0 8px 8px}
.package svg{position:absolute;left:0;top:0}
.package .pname{position:absolute;left:0;width:100%;text-align:center;color:var(--red);font-weight:900;font-size:21px;line-height:20px}
.package .pitems{position:absolute;left:0;width:100%;text-align:center;color:var(--white);font-weight:600;font-size:12.5px;line-height:14px;list-style:none;white-space:nowrap}
.package .pprice{position:absolute;left:0;width:100%;top:182px;text-align:center;color:var(--white);font-size:11.5px;letter-spacing:1.5px;font-weight:500}
.tab{position:absolute;top:554px;height:91px;color:var(--white)}
.tab svg{position:absolute;left:0;top:0}
.tab .tname{position:absolute;top:5px;font-size:19px;font-weight:900;font-style:italic}
.tab .qty{position:absolute;font-size:11.5px;font-weight:700;line-height:12px}
.tab .qty span{display:block;font-weight:500;letter-spacing:1.5px;font-size:10px}
.item{position:absolute;top:559px;color:var(--red);white-space:nowrap}
.item .iname{font-size:19px;font-weight:900;line-height:20px}
.item .isize{font-size:11.5px;font-weight:600;margin-top:2px}
.item .iprice{font-size:10.5px;letter-spacing:1.5px;font-weight:500}
.learn{position:absolute;left:400px;top:660px;width:400px;height:21px;border:1.5px solid var(--navy);background:var(--white);border-radius:2px;color:var(--navy);font-size:12px;letter-spacing:.6px;text-align:center;line-height:18px;font-weight:500;white-space:nowrap;overflow:hidden}
.learn b{font-weight:800}
.cursor{position:absolute;left:792px;top:668px}
</style>
</head>
<body>
<div class="board">
  <div class="photo photo-top" role="img" aria-label="Platters of fried chicken wings, ribs and onion rings on a wooden table"></div>
  <div class="photo photo-bottom" role="img" aria-label="Platters of sauced chicken tenders, waffle fries, celery and hands reaching for food"></div>
  <div class="panel"></div>
  <div class="photo photo-platter" role="img" aria-label="Tray of crispy chicken tenders"></div>

  <h1 class="title">CATERING MENU</h1>

  <h2 class="section-head" style="left:130px;top:270px">PER PERSON DEAL<span class="rule" style="width:200px"></span></h2>
  <p class="note">&#9656; A MINIMUM OF 10 PEOPLE ARE NEEDED FOR THE PER PERSON DEALS</p>

  <div class="option" style="left:177px">
    <svg class="notch" viewBox="0 0 20 160" width="20" height="160"><path d="M0 0 L20 30 L0 50 Z" fill="#e0a91e"/><rect x="4" y="50" width="4" height="110" fill="#f2bd24"/></svg>
    <div class="label">OPTION 1</div><div class="name">SNACK</div>
    <ul class="items"><li>2 TENDERS</li><li>SAUCE</li><li>DRESSING</li><li>1 REG SIDE</li></ul>
    <div class="price">$7.00/PERSON</div>
  </div>
  <div class="option" style="left:336px">
    <svg class="notch" viewBox="0 0 20 160" width="20" height="160"><path d="M0 0 L20 30 L0 50 Z" fill="#e0a91e"/><rect x="4" y="50" width="4" height="110" fill="#f2bd24"/></svg>
    <div class="label">OPTION 2</div><div class="name">PARTY</div>
    <ul class="items"><li>2 TENDERS</li><li>3 WINGS</li><li>SAUCE</li><li>DRESSING</li><li>1 REG SIDE</li><li>12OZ DRINK</li></ul>
    <div class="price">$11.00/PERSON</div>
  </div>
  <div class="option" style="left:491px">
    <svg class="notch" viewBox="0 0 20 160" width="20" height="160"><path d="M0 0 L20 30 L0 50 Z" fill="#e0a91e"/><rect x="4" y="50" width="4" height="110" fill="#f2bd24"/></svg>
    <div class="label">OPTION 3</div><div class="name">FEAST</div>
    <ul class="items"><li>2 TENDERS</li><li>6 WINGS</li><li>SAUCE</li><li>DRESSING</li><li>1 REG SIDE</li><li>20OZ DRINK</li></ul>
    <div class="price">$15.00/PERSON</div>
  </div>

  <h2 class="section-head" style="left:670px;top:270px">PACKAGE DEALS<span class="rule" style="width:165px;margin-left:8px"></span></h2>

  <div class="package" style="left:670px;width:130px">
    <svg width="130" height="66" viewBox="0 0 130 66"><path d="M0 0H130V56H75L65 66L55 56H0Z" fill="#fff"/></svg>
    <div class="pname" style="top:20px">FAMILY</div>
    <ul class="pitems" style="top:93px"><li>12 TENDERS</li><li>SAUCES</li><li>DRESSING</li><li>LARGE SIDE</li><li>2L</li></ul>
    <div class="pprice">$24.99</div>
  </div>
  <div class="package" style="left:813px;width:129px">
    <svg width="129" height="66" viewBox="0 0 129 66"><path d="M0 0H129V56H74L64.5 66L55 56H0Z" fill="#fff"/></svg>
    <div class="pname" style="top:20px">TAILGATE</div>
    <ul class="pitems" style="top:76px"><li>20 TENDERS</li><li>30 WINGS</li><li>SAUCES</li><li>2 PARTY SIDES</li><li>2 PARTY SALADS</li><li>DRESSINGS</li><li>2 2L</li></ul>
    <div class="pprice" style="top:180px">$75.99</div>
  </div>
  <div class="package" style="left:954px;width:128px">
    <svg width="128" height="66" viewBox="0 0 128 66"><path d="M0 0H128V56H74L64 66L54 56H0Z" fill="#fff"/></svg>
    <div class="pname" style="top:10px">HOUSE<br>PARTY</div>
    <ul class="pitems" style="top:76px"><li>20 TENDERS</li><li>60 WINGS</li><li>SAUCES</li><li>2 PARTY SIDES</li><li>2 PARTY SALADS</li><li>DRESSINGS</li><li>2 2L</li></ul>
    <div class="pprice">$155.99</div>
  </div>

  <h2 class="section-head" style="left:130px;top:524px">MAKE YOUR OWN DEAL<span class="rule" style="width:604px;margin-left:14px"></span></h2>

  <div class="tab" style="left:162px;width:110px">
    <svg width="110" height="91" viewBox="0 0 110 91"><path d="M0 0H110V89Q110 91 108 91H20V20Z" fill="#d43b2c"/></svg>
    <div class="tname" style="left:26px">WINGS</div>
    <div class="qty" style="left:26px;top:30px">50<span>$7.00</span></div>
    <div class="qty" style="left:73px;top:30px">75<span>$XX</span></div>
    <div class="qty" style="left:26px;top:59px">100<span>$XX</span></div>
  </div>
  <div class="tab" style="left:316px;width:136px">
    <svg width="136" height="91" viewBox="0 0 136 91"><path d="M0 0H136V89Q136 91 134 91H18V20Z" fill="#d43b2c"/></svg>
    <div class="tname" style="left:28px">TENDERS</div>
    <div class="qty" style="left:28px;top:30px">30<span>$7.00</span></div>
    <div class="qty" style="left:75px;top:30px">45<span>$XX</span></div>
    <div class="qty" style="left:28px;top:59px">60<span>$XX</span></div>
  </div>

  <div class="item" style="left:506px"><div class="iname">WAFFLE<br>FRIES</div><div class="isize">PARTY SIZE</div><div class="iprice">$13.99</div></div>
  <div class="item" style="left:655px"><div class="iname">GARLIC<br>PARM<br>TOTS</div><div class="isize">PARTY SIZE</div><div class="iprice">$13.99</div></div>
  <div class="item" style="left:797px;top:561px"><div class="iname">CHICKEN<br>CAESAR<br>SALAD</div><div class="isize">PARTY SIZE</div><div class="iprice">$38.99</div></div>
  <div class="item" style="left:957px"><div class="iname">CAESAR<br>SALAD</div><div class="isize">PARTY SIZE</div><div class="iprice">$27.99</div></div>

  <div class="learn">LEARN MORE AT <b>CRISPHARBOR-EATS.EXAMPLE/MENU</b></div>
  <svg class="cursor" width="26" height="28" viewBox="0 0 26 28" aria-hidden="true">
    <path d="M3 3L21 15L13 16L18 25L14 27L9 18L3 23Z" fill="#fff" stroke="#d43b2c" stroke-width="2" stroke-linejoin="round"/>
  </svg>
</div>
</body>
</html>
```